Kesso Tea Premium Matcha brand Label

This is a label design project for a luxury tea brand. Feel free to be creative within the guidelines.
Attached to this project is a document called “Private Label Design Requirements” with the design guidelines and template. There is another document called "Kesso Tea Packaging Instructions" this has more details necessary to stick to the guidelines in the first document.

I have also attached the certifications to be included as well as different variations of the logo for you to use.

If you have any questions, I am here.
Updates

Need extra days to review

Target Market(s)

Young, active, fun, enjoy the finer things

```html
<!DOCTYPE html>
<html lang="en">
<head>
<meta charset="utf-8">
<title>Kesso Tea – Premium Organic Ceremonial Matcha Label</title>
<link href="https://fonts.googleapis.com/css2?family=Montserrat:wght@300;400;500;600;700&display=swap" rel="stylesheet">
<style>
  :root {
    --page-bg: #ffffff;
    --label-bg: #f1f1f1;
    --ink: #111111;
    --ink-soft: #2a2a2a;
    --matcha: #6cc04a;
    --matcha-deep: #4e9a34;
    --band: #000000;
    --white: #ffffff;
    --badge-blue: #1f5fa8;
    --badge-green: #2f8a3c;
  }
  * { box-sizing: border-box; margin: 0; padding: 0; }
  html, body { width: 1200px; height: 996px; overflow: hidden; background: var(--page-bg); }
  body { position: relative; font-family: "Montserrat", sans-serif; color: var(--ink); }

  .label {
    position: absolute; left: 30px; top: 403px;
    width: 1140px; height: 190px;
    background: var(--label-bg);
    box-shadow: 0 6px 22px rgba(0,0,0,0.14);
  }

  .brand { position: absolute; display: flex; align-items: center; gap: 6px; }
  .brand-dot { width: 12px; height: 12px; border-radius: 50%; background: var(--matcha); flex: none; }
  .brand-name { font-size: 15px; font-weight: 700; color: var(--ink); white-space: nowrap; }
  .brand--side { left: 16px; top: 40px; }
  .brand--center { left: 570px; top: 40px; transform: translateX(-50%); }

  .origin { position: absolute; left: 16px; top: 111px; width: 200px; }
  .origin-title {
    font-size: 13px; font-weight: 600; letter-spacing: 0.01em;
    display: inline-block; padding-bottom: 3px;
    background: linear-gradient(var(--ink), var(--ink)) left bottom / 64px 1px no-repeat;
  }
  .origin-dist { margin-top: 4px; font-size: 10.5px; font-weight: 500; line-height: 1.05; }
  .origin-cert { margin-top: 7px; font-size: 7.5px; font-weight: 400; }

  .title-frame {
    position: absolute; left: 367px; top: 87px; width: 404px; height: 74px;
    border: 3px solid var(--matcha); padding: 5px;
    background: var(--white);
  }
  .title-box {
    width: 100%; height: 100%; background: var(--band); color: var(--white);
    display: flex; flex-direction: column; align-items: center; justify-content: center;
  }
  .title-main { font-size: 23px; font-weight: 700; letter-spacing: 0.06em; line-height: 1; }
  .title-sub { font-size: 17px; font-weight: 300; letter-spacing: 0.04em; line-height: 1.1; margin-top: 2px; }

  .net-wt { position: absolute; left: 570px; top: 169px; transform: translateX(-50%); font-size: 9.5px; font-weight: 400; color: var(--ink-soft); }

  .info { position: absolute; left: 938px; top: 11px; width: 190px; }
  .info-title { font-size: 10.5px; font-weight: 600; line-height: 1.1; }
  .info-head { margin-top: 9px; font-size: 8px; font-weight: 700; letter-spacing: 0.02em; }
  .info-list { list-style: none; margin-top: 3px; }
  .info-list li { font-size: 7.3px; line-height: 1.42; color: var(--ink-soft); }
  .info-list li::before { content: "• "; }

  .cert { position: absolute; }
  .cert--square { left: 941px; top: 115px; width: 74px; height: 56px; background: var(--badge-blue); border-bottom: 10px solid var(--badge-green); }
  .cert--round { left: 1033px; top: 112px; width: 62px; height: 62px; border-radius: 50%; background: var(--white); border: 3px solid var(--badge-green); }
</style>
</head>
<body>
  <section class="label" aria-label="Kesso Tea matcha jar label">
    <div class="brand brand--side">
      <span class="brand-dot"></span>
      <span class="brand-name">Kesso Tea</span>
    </div>

    <div class="origin">
      <p class="origin-title">PRODUCT OF JAPAN</p>
      <p class="origin-dist">Distributed by Kesso Tea Co.<br>Brookvale, Ga</p>
      <p class="origin-cert">Certified Organic by Verdana Certifiers</p>
    </div>

    <div class="brand brand--center">
      <span class="brand-dot"></span>
      <span class="brand-name">Kesso Tea</span>
    </div>

    <div class="title-frame">
      <div class="title-box">
        <span class="title-main">PREMIUM ORGANIC</span>
        <span class="title-sub">CEREMONIAL MATCHA</span>
      </div>
    </div>
    <p class="net-wt">Net Wt: 30g</p>

    <div class="info">
      <p class="info-title">Premium Organic Japanese<br>Matcha Green Tea</p>
      <p class="info-head">INSTRUCTIONS</p>
      <ul class="info-list">
        <li>2 tsp of Matcha</li>
        <li>2oz of Water (170-180 degrees F)</li>
        <li>Whisk in a W formation until frothy</li>
        <li>Sweeten to taste</li>
      </ul>
    </div>

    <div class="cert cert--square" role="img" aria-label="Non-GMO verification badge"></div>
    <div class="cert cert--round" role="img" aria-label="Organic certification seal"></div>
  </section>
</body>
</html>
```